Financial Advisor Resource Firm needs business card design

Need business card design for company in Omaha NE called Meridale Circle. We provide resources to financial advisors....workshop programs, retirement analysis, and insurance planning. I would like to see designs that use grays, greens, black, and white colors. The final design should communicate 'collaboration' and be simple yet attractive to financial planning clients. I will attached our logo and another picture of a puzzle piece coming together. I would like the incorporate the puzzle picture somehow, maybe on the back somehow, with color or just the gray scale....OR, the picture be the front of the card with 'Meridale' definition on it (see upload) and then company logo, employee name, title, address on the back (see ppt uploaded). The following disclosure needs to be included somewhere- Advisory services offered through Stonebrook Assets, LLC.
Updates

I uploaded a svg and ai file of the logo

Target Market(s)

Financial planning clients and financial advisors....so pretty diverse age range of about 40-70.

Industry/Entity Type

Financial Planning

Contact Information for Business Card

Tobias L. Fenwright, MBA
Founder/President
5287 E. Larkin Road
Suite 230
Omaha, NE 68190
Phone- (402) 555-0147
Cell- (402) 555-0183
Fax- (402) 555-0129
email- tobias@meridaleplan.example
web address- www.meridaleplan.example

Colors
1b1b1b
474747
d3d3d3
ffffff
9bcb3c
abd036

Requirements
Must have
• Must include logo provided, must be 2 sided, and must have disclosure...all of these items listed in project description

```html
<!DOCTYPE html>
<html lang="en">
<head>
<meta charset="utf-8">
<title>Meridale Circle — Business Card</title>
<link rel="stylesheet" href="https://fonts.googleapis.com/css2?family=Montserrat:wght@400;500;600&display=swap">
<style>
  :root {
    --page: #f4f4f4;
    --card: #1b1b1b;
    --green: #9bcb3c;
    --white: #ffffff;
    --gray: #d3d3d3;
  }
  * { margin: 0; padding: 0; box-sizing: border-box; }
  html, body {
    width: 1200px; height: 900px; overflow: hidden;
    background: var(--page);
    font-family: "Montserrat", Arial, sans-serif;
  }
  .card {
    position: absolute; left: 296px; width: 608px; height: 348px;
    background: var(--card); overflow: hidden;
    box-shadow: 0 12px 30px rgba(0,0,0,0.28);
    color: var(--white);
  }
  .card--front { top: 89px; }
  .card--back { top: 482px; }
  .accent { color: var(--green); }

  .wordmark { display: flex; align-items: center; gap: 8px; color: var(--white);
    font-weight: 500; letter-spacing: 1.5px; text-transform: uppercase; white-space: nowrap; }
  .wordmark__dot { width: 12px; height: 12px; border-radius: 50%; background: var(--green); flex: none; }

  .card--front .wordmark { position: absolute; left: 0; right: 0; top: 162px;
    justify-content: center; font-size: 23px; }
  .tagline { position: absolute; left: 0; right: 0; top: 286px; text-align: center;
    font-size: 14.5px; line-height: 21px; }
  .tagline strong { font-weight: 500; color: var(--green); }

  .card--back .wordmark { position: absolute; left: 36px; top: 48px; font-size: 20px; }
  .holder { position: absolute; right: 36px; top: 44px; text-align: right; }
  .holder__name { font-size: 18px; color: var(--green); font-weight: 500; }
  .holder__cred { font-size: 13px; color: var(--white); }
  .holder__title { font-size: 14px; margin-top: 2px; }
  .address { position: absolute; left: 36px; top: 94px; color: var(--green);
    font-size: 14.5px; line-height: 20px; font-style: normal; }
  .contacts { position: absolute; left: 36px; top: 144px; list-style: none; }
  .contacts li { display: flex; align-items: center; height: 26px; font-size: 15px; letter-spacing: 0.3px; white-space: nowrap; }
  .contacts svg { width: 18px; height: 18px; margin-right: 12px; fill: var(--green); }

  .disclosure { position: absolute; left: 36px; bottom: 12px; font-size: 10px;
    letter-spacing: 0.3px; color: var(--white); }

  .photo-band { position: absolute; left: 0; top: 0; width: 608px; height: 348px; }
</style>
</head>
<body>
  <section class="card card--front">
    <div class="wordmark"><span class="wordmark__dot"></span>Meridale Circle</div>
    <p class="tagline">To come <strong>TOGETHER</strong> and <strong>UNITE</strong> in common interest and <strong>FOCUS</strong><br>www.<span class="accent">meridaleplan</span>.example</p>
  </section>

  <section class="card card--back">
    <svg class="photo-band" viewBox="0 0 608 348">
      <defs>
        <linearGradient id="bandTone" x1="0" y1="1" x2="1" y2="0">
          <stop offset="0" stop-color="#5fae4a"/>
          <stop offset="0.45" stop-color="#2f6e3a"/>
          <stop offset="0.75" stop-color="#b9d7a4"/>
          <stop offset="1" stop-color="#e6eee0"/>
        </linearGradient>
      </defs>
      <path role="img" aria-label="Green-tinted photo of hands joining puzzle pieces"
            d="M0 293 C150 318 300 308 400 258 S560 118 608 108 L608 348 L0 348 Z" fill="url(#bandTone)"/>
      <path d="M0 285 C150 310 300 300 400 250 S560 110 608 100" fill="none" stroke="#9bcb3c" stroke-width="3"/>
    </svg>

    <div class="wordmark"><span class="wordmark__dot"></span>Meridale Circle</div>
    <div class="holder">
      <div class="holder__name">Tobias L. Fenwright, <span class="holder__cred">MBA</span></div>
      <div class="holder__title">Founder | President</div>
    </div>
    <address class="address">5287 E. Larkin Road<br>Suite 230, Omaha, NE 68190</address>
    <ul class="contacts">
      <li><svg viewBox="0 0 24 24"><path d="M6.6 10.8a15 15 0 0 0 6.6 6.6l2.2-2.2c.3-.3.7-.4 1-.2 1.1.4 2.3.6 3.6.6.6 0 1 .4 1 1V20c0 .6-.4 1-1 1A17 17 0 0 1 3 4c0-.6.4-1 1-1h3.5c.6 0 1 .4 1 1 0 1.3.2 2.5.6 3.6.1.3 0 .7-.2 1z"/></svg>(402) 555 - 0147</li>
      <li><svg viewBox="0 0 24 24"><path d="M7 1h10a2 2 0 0 1 2 2v18a2 2 0 0 1-2 2H7a2 2 0 0 1-2-2V3a2 2 0 0 1 2-2zm0 3v14h10V4zm5 15.5a1 1 0 1 0 0 2 1 1 0 0 0 0-2z"/></svg>(402) 555 - 0183</li>
      <li><svg viewBox="0 0 24 24"><path d="M3 6h4v16H3zM9 2h9l3 3v17H9zm2 3v5h8V5zm1 8v2h2v-2zm4 0v2h2v-2zm-4 4v2h2v-2zm4 0v2h2v-2z"/></svg>(402) 555 - 0129</li>
      <li><svg viewBox="0 0 24 24"><path d="M2 5h20v14H2zm2 2v.5l8 5 8-5V7z"/></svg>tobias@<span class="accent">meridaleplan</span>.example</li>
    </ul>
    <p class="disclosure">Advisory services offered through Stonebrook Assets, LLC</p>
  </section>
</body>
</html>
```